Velmora Systems Website

Website design for our company: Velmora Systems.
The website should look fresh and IT focused. Please have a look at http://www.velmorasystems.example.au/ for our current design. We want something fresh and new, professional looking, in WordPress so we can easily make changes.

It Company

```html
<!DOCTYPE html>
<html lang="en">
<head>
<meta charset="utf-8">
<title>Velmora Systems</title>
<link href="https://fonts.googleapis.com/css2?family=Open+Sans:wght@300;400;600;700&display=swap" rel="stylesheet">
<style>
:root{
  --green:#0db14b;
  --header:#3d3f45;
  --footer:#43454b;
  --blue:#2f8fe0;
  --text:#3b3b3b;
  --footer-text:#dadbdd;
  --footer-head:#c4c6c9;
  --quote:#8e9196;
  --white:#ffffff;
}
*{box-sizing:border-box;margin:0;padding:0}
html,body{width:1024px;height:1200px;overflow:hidden}
body{position:relative;background:#fbfcfc;font-family:"Open Sans",sans-serif;color:var(--text)}
.abs{position:absolute}
.top-strip{left:0;top:0;width:1024px;height:5px;background:var(--green)}
.site-header{left:0;top:5px;width:1024px;height:78px;background:linear-gradient(#44464c,#35373c);border-bottom:2px solid #e8e8e8}
.brand{display:flex;align-items:center;justify-content:center;gap:6px;background:var(--green);border:3px solid #fff;border-top:none;border-radius:0 0 4px 4px;color:#fff;font-weight:700;font-size:14px}
.brand-dot{width:12px;height:12px;border-radius:50%;background:#fff}
.header-brand{left:138px;top:5px;width:148px;height:69px}
.search{left:733px;top:17px;width:139px;height:18px;background:#fff;border-radius:2px;font-size:8px;color:#777;padding:3px 0 0 20px}
.search svg{position:absolute;left:5px;top:4px}
.main-nav{left:317px;top:42px;display:flex;align-items:center;font-size:12.5px;font-weight:700;color:#fff}
.main-nav a{color:#fff;text-decoration:none;margin-right:37px}
.main-nav a.current{background:var(--blue);border:1px solid #79b8ef;border-radius:3px;padding:4px 12px;margin-right:28px}
.hero-visual{left:0;top:85px;width:1024px;height:362px;background:radial-gradient(circle at 68% 35%,#f3d27a 0,#d99a57 8%,rgba(70,140,200,0) 22%),linear-gradient(100deg,#0c4f9e 0%,#1a6cc2 35%,#4e9ad8 60%,#2a5f9e 100%)}
.hero-card{left:135px;top:126px;width:238px;height:278px;background:var(--green);color:#fff;padding:34px 8px 0 24px}
.hero-card h1{font-size:23px;line-height:29px;font-weight:700;letter-spacing:-0.2px}
.hero-card p{font-size:11px;line-height:16px;margin-top:11px;padding-right:4px}
.dots{position:absolute;left:32px;top:236px;display:flex;gap:8px}
.dots span{width:8px;height:8px;border-radius:50%;background:#5fd08a}
.dots span:first-child{background:#fff}
.support-band{left:0;top:447px;width:1024px;height:84px;background:radial-gradient(ellipse at 40% 0,#3ccb78,var(--green) 70%)}
.support-band h2{position:absolute;left:162px;top:18px;font-size:23px;font-weight:300;color:#fff}
.support-band p{position:absolute;left:162px;top:45px;font-size:14.5px;color:#fff}
.code-input{left:616px;top:477px;width:176px;height:30px;background:#fff;font-size:12px;color:#666;padding:8px 10px}
.connect{left:800px;top:477px;width:86px;height:30px;background:var(--blue);border:1px solid #8cc4f3;border-radius:2px;color:#fff;font-size:12px;font-weight:700;text-align:center;line-height:28px}
.section-title{font-size:19.5px;font-weight:300;color:#444}
.avatar{border-radius:50%;background:radial-gradient(#c9c9c9,#8b8b8b);border:3px solid #fff;box-shadow:0 0 0 1px #ccc}
.body-copy{font-size:10.5px;line-height:16px;color:#444}
.read-more{left:224px;top:690px;width:82px;height:27px;background:linear-gradient(#f2f2f2,#dcdcdc);border-radius:3px;box-shadow:0 1px 1px #aaa;font-size:7.5px;text-align:center;line-height:27px;color:#555}
.quote-box{left:617px;top:610px;width:276px;height:103px;background:var(--quote);border-radius:3px;border-bottom:4px solid #c5c6c9;color:#fff;font-size:10.5px;line-height:16px;padding:18px 25px}
.quote-tail{left:599px;top:624px;width:0;height:0;border-right:18px solid var(--quote);border-bottom:22px solid transparent}
.name{left:526px;top:665px;font-size:8.5px;font-weight:700;color:#333}
.role{left:526px;top:676px;font-size:7px;color:#333;white-space:nowrap}
.rule{left:141px;top:805px;width:752px;height:2px;background:#ddd}
.notch{left:512px;top:806px;border-left:6px solid transparent;border-right:6px solid transparent;border-top:6px solid #ddd}
.service{display:flex;align-items:center;gap:10px;font-size:11.5px;font-weight:700;color:#333;line-height:16px}
.service .icon{width:32px;height:32px;border-radius:50%;background:#3f4146;display:flex;align-items:center;justify-content:center;flex-shrink:0}
.service.active{color:#2a6db5}
.service.active .icon{background:var(--blue);box-shadow:0 0 0 2px #bcd9f4}
.site-footer{left:0;top:977px;width:1024px;height:216px;background:var(--footer)}
.bottom-strip{left:0;top:1193px;width:1024px;height:7px;background:var(--green)}
.footer-brand{left:142px;top:1011px;width:150px;height:76px;border:3px solid #fff;border-radius:3px}
.footer-head{font-size:11.5px;font-weight:700;color:var(--footer-head)}
.footer-list{list-style:none;font-size:10px;line-height:16px;color:var(--footer-text)}
.footer-list li::before{content:"";display:inline-block;border-left:4px solid #ccc;border-top:3px solid transparent;border-bottom:3px solid transparent;margin-right:5px}
.footer-text{font-size:10.5px;line-height:16px;color:var(--footer-text)}
.copyright{left:142px;top:1137px;font-size:9px;color:#8a8c90}
.footer-input{left:718px;top:1066px;width:175px;height:27px;border:1px solid #2e2f33;background:#3a3c41;border-radius:3px}
.footer-input span{position:absolute;right:2px;top:2px;width:55px;height:21px;background:#4c4e53;border-radius:2px;font-size:7.5px;text-align:center;line-height:21px;color:#ccc}
.social{left:718px;top:1138px;display:flex;gap:15px}
.social span{width:13px;height:13px;border-radius:50%;background:#707277}
</style>
</head>
<body>
<div class="abs top-strip"></div>
<header class="abs site-header"></header>
<div class="abs brand header-brand"><span class="brand-dot"></span>Velmora Systems</div>
<div class="abs search"><svg width="8" height="8" viewBox="0 0 8 8"><circle cx="3.3" cy="3.3" r="2.5" fill="none" stroke="#888"/><line x1="5" y1="5" x2="7.5" y2="7.5" stroke="#888"/></svg>Search Site</div>
<nav class="abs main-nav">
  <a class="current">Home</a><a>Services</a><a>Support</a><a>Clients</a><a>Testimonial</a><a>About</a><a>Contact</a>
</nav>

<div class="abs hero-visual" role="img" aria-label="Hand touching a glowing digital world map interface"></div>
<div class="abs hero-card">
  <h1>We will bring your businesses forward</h1>
  <p>Velmora Systems is an Adelaide based company with a single objective - to excel in the support and service of all computer and IT needs.</p>
  <div class="dots"><span></span><span></span><span></span><span></span></div>
</div>

<section class="abs support-band">
  <h2>Remote Support</h2>
  <p>Need help? Connect to our friendly staff to assist you.</p>
</section>
<div class="abs code-input">Enter 6-digit Code</div>
<div class="abs connect">Connect</div>

<h2 class="abs section-title" style="left:142px;top:566px">WELCOME TO OUR SITE!</h2>
<div class="abs avatar" style="left:142px;top:607px;width:70px;height:70px" role="img" aria-label="Portrait of a smiling team member"></div>
<p class="abs body-copy" style="left:223px;top:605px;width:252px">Because we know you don't want to be limited on a portrait or scape format we made Showcase. compatible in both portrait AND landscape! Yes, we care about you.</p>
<div class="abs read-more">READ MORE</div>

<h2 class="abs section-title" style="left:526px;top:566px">WHAT PEOPLE SAY</h2>
<div class="abs avatar" style="left:526px;top:607px;width:53px;height:53px" role="img" aria-label="Portrait of a client"></div>
<div class="abs name">MARA QUILL</div>
<div class="abs role">CEO, QUILL.EXAMPLE</div>
<div class="abs quote-tail"></div>
<div class="abs quote-box">Because we know you don't want to be limited on a portrait or scape format we made Showcase. compatible in both portrait AND landscape!</div>

<h2 class="abs section-title" style="left:0;top:762px;width:1010px;text-align:center">OUR SERVICES</h2>
<div class="abs rule"></div>
<div class="abs notch"></div>

<div class="abs service active" style="left:141px;top:833px"><span class="icon"><svg width="16" height="16" viewBox="0 0 16 16"><circle cx="8" cy="8" r="7" fill="#fff"/><rect x="4" y="7" width="8" height="2" fill="#2f8fe0"/></svg></span>ON-SITE SERVICE</div>
<div class="abs service" style="left:333px;top:833px"><span class="icon"><svg width="14" height="14" viewBox="0 0 14 14"><rect x="2" y="2" width="10" height="10" fill="none" stroke="#fff" stroke-width="1.6"/></svg></span>MEDICAL IT SERVICE</div>
<div class="abs service" style="left:526px;top:833px"><span class="icon"><svg width="16" height="16" viewBox="0 0 16 16"><circle cx="8" cy="8" r="6.5" fill="none" stroke="#fff" stroke-width="1.6"/><line x1="1.5" y1="8" x2="14.5" y2="8" stroke="#fff"/></svg></span>REMOTE DESKTOP</div>
<div class="abs service" style="left:718px;top:833px"><span class="icon"><svg width="14" height="14" viewBox="0 0 14 14"><path d="M5 1h4v4l4 8H1l4-8z" fill="#fff"/></svg></span>PHARMACY IT SERVICE</div>
<div class="abs service" style="left:141px;top:891px"><span class="icon"><svg width="14" height="14" viewBox="0 0 14 14"><rect x="3" y="1" width="8" height="12" fill="none" stroke="#fff" stroke-width="1.5"/></svg></span>HARDWARE/ SOFTWARE<br>SUPPLY</div>
<div class="abs service" style="left:333px;top:891px"><span class="icon"><svg width="14" height="14" viewBox="0 0 14 14"><path d="M2 12L11 2l1 1L4 12z" fill="#fff"/></svg></span>WEBSITE DESIGN</div>
<div class="abs service" style="left:526px;top:891px"><span class="icon"><svg width="14" height="14" viewBox="0 0 14 14"><path d="M7 1l6 6-6 6-6-6z" fill="#fff"/></svg></span>DISASTER RECOVERY</div>
<div class="abs service" style="left:718px;top:891px"><span class="icon"><svg width="14" height="14" viewBox="0 0 14 14"><g stroke="#fff" stroke-width="1.6"><line x1="3" y1="2" x2="3" y2="12"/><line x1="6" y1="2" x2="6" y2="12"/><line x1="9" y1="2" x2="9" y2="12"/><line x1="12" y1="2" x2="12" y2="12"/></g></svg></span>CONSUMABLES</div>

<footer class="abs site-footer"></footer>
<div class="abs brand footer-brand"><span class="brand-dot"></span>Velmora Systems</div>
<div class="abs copyright">© 2014 Velmora Systems. All Rights Reserved</div>

<div class="abs footer-head" style="left:370px;top:1012px">NAVIGATION</div>
<ul class="abs footer-list" style="left:370px;top:1041px">
  <li>HOME</li><li>CLIENTS</li><li>SERVICES</li><li>SUPPORTS</li><li>TESTIMONIALS</li><li>CONTACT US</li><li>ABOUT US</li>
</ul>

<div class="abs footer-head" style="left:526px;top:1012px">CONTACTS</div>
<p class="abs footer-text" style="left:526px;top:1040px">Harbourline Pty Ltd<br>PO Box 40962<br>Wattle Grove Lane, Fernhill<br>Victoria 3999 Australia</p>
<p class="abs footer-text" style="left:526px;top:1120px">Phone: (03) 5550 1842<br>help@velmorasystems.example</p>

<div class="abs footer-head" style="left:718px;top:1012px">REMOTE SUPPORT</div>
<p class="abs footer-text" style="left:718px;top:1041px;font-size:9.5px">Enter you 6-digit code</p>
<div class="abs footer-input"><span>CONNECT</span></div>
<div class="abs footer-head" style="left:718px;top:1112px">GET SOCIAL</div>
<div class="abs social"><span></span><span></span><span></span><span></span><span></span></div>

<div class="abs bottom-strip"></div>
</body>
</html>
```